Classy, Elegant, Simple Business Card Design

Looking to have a classy, simple, and elegant design. Want a top notch designed business card. I really like the look of the new torvane credit card. I also like the design I attached. I am trying to reach 21-29 year old females for booking us for there wedding or event. We offer Disc Jockey Service, Photo Booth Rentals, and Uplighting .

Target Market(s)

21-28 year old females

Contact Information for Business Card

Has to have logo, website, email, and phone number

Font styles to use
Other font styles liked:
• open to font choice, modern, clean
Designer to choose
33a6d7
0791cd
0555a3
ffffff

Requirements
Must have
• Has to have logo, website, email, and phone number
Nice to have
• I really like the design of the new torvane credit card. I also included my logo and some designs I like
Should not have
• clutter or too much info

```html
<!DOCTYPE html>
<html lang="en">
<head>
<meta charset="utf-8">
<title>Tidemark Events – Business Card</title>
<link rel="stylesheet" href="https://fonts.googleapis.com/css2?family=Poppins:wght@400;500&display=swap">
<style>
  :root {
    --backdrop: #1c1c1c;
    --card-white: #ffffff;
    --brand-blue: #0791cd;
    --bright-blue: #33a6d7;
    --deep-blue: #0555a3;
    --navy: #1d3557;
    --text-dark: #3a3a3a;
    --text-grey: #8a8a8a;
    --rule-grey: #555555;
    --mark-light: #e4e7ea;
  }
  * { margin: 0; padding: 0; box-sizing: border-box; }
  html, body {
    width: 1200px; height: 1200px; overflow: hidden;
    background: var(--backdrop);
    font-family: "Poppins", sans-serif;
  }
  .card {
    position: absolute; left: 262px; width: 686px; height: 392px;
    overflow: hidden;
  }
  .card--front { top: 165px; background: var(--card-white); }
  .card--back {
    top: 653px;
    background: radial-gradient(ellipse at 50% 45%, #06a8e6 0%, #1590d4 55%, #1b7ec6 100%);
  }
  .brand-name {
    position: absolute; right: 42px; top: 118px;
    display: flex; align-items: center; gap: 10px;
    font-size: 26px; font-weight: 500; color: var(--brand-blue);
    letter-spacing: 0.5px;
  }
  .brand-dot { width: 12px; height: 12px; border-radius: 50%; background: var(--brand-blue); }
  .holder { position: absolute; left: 37px; top: 247px; }
  .holder-name { font-size: 24px; font-weight: 500; color: var(--brand-blue); line-height: 1.2; }
  .holder-role { font-size: 16px; color: var(--text-grey); line-height: 1.2; }
  .divider {
    position: absolute; left: 37px; top: 305px; width: 607px; height: 1px;
    background: var(--rule-grey);
  }
  .contact { position: absolute; left: 37px; top: 318px; list-style: none; }
  .contact li {
    display: flex; align-items: center; gap: 8px;
    font-size: 16px; color: var(--text-dark); line-height: 20px;
  }
  .contact svg { width: 13px; height: 13px; fill: var(--brand-blue); }
  .footer-bands { position: absolute; left: 0; bottom: 0; width: 686px; height: 30px; }
  .website {
    position: absolute; right: 34px; bottom: 5px;
    font-size: 16px; color: var(--card-white);
  }
  .back-name {
    position: absolute; left: 0; right: 0; top: 150px; text-align: center;
    font-size: 64px; font-weight: 500; color: var(--mark-light);
  }
  .services {
    position: absolute; left: 0; right: 0; top: 336px; text-align: center;
    font-size: 16px; font-weight: 500; color: var(--card-white);
  }
</style>
</head>
<body>
  <section class="card card--front">
    <div class="brand-name"><span class="brand-dot"></span>Tidemark Events</div>
    <div class="holder">
      <p class="holder-name">Daniel Brooks</p>
      <p class="holder-role">President</p>
    </div>
    <div class="divider"></div>
    <ul class="contact">
      <li><svg viewBox="0 0 24 24"><path d="M6.6 10.8a15.1 15.1 0 0 0 6.6 6.6l2.2-2.2c.3-.3.7-.4 1-.2 1.1.4 2.3.6 3.6.6.6 0 1 .4 1 1V20c0 .6-.4 1-1 1A17 17 0 0 1 3 4c0-.6.4-1 1-1h3.5c.6 0 1 .4 1 1 0 1.3.2 2.5.6 3.6.1.3 0 .7-.2 1z"/></svg>555-214-0387</li>
      <li><svg viewBox="0 0 24 24"><path d="M2 5h20v14H2z M4 7v.5l8 5 8-5V7l-8 5z" fill-rule="evenodd"/></svg>info@tidemarkevents.com</li>
    </ul>
    <svg class="footer-bands" viewBox="0 0 686 30" preserveAspectRatio="none">
      <polygon points="0,13 426,13 422,18 0,18" fill="var(--navy)"/>
      <polygon points="0,22 686,22 686,30 0,30" fill="var(--brand-blue)"/>
      <polygon points="445,0 686,0 686,30 420,30" fill="var(--brand-blue)"/>
    </svg>
    <span class="website">www.tidemarkevents.com</span>
  </section>

  <section class="card card--back">
    <p class="back-name">Tidemark Events</p>
    <p class="services">Disc Jockey Service • Photo Booth Rentals • Uplighting .</p>
  </section>
</body>
</html>
```